Need App for Impact Related Events

My app is to help with internal events. When you enter the prompted event code the next screen shows you everyone currently at the event. It will give you the ability to Start a conversation with someone you met at that event, or signal it is your turn to send a message. The next screen is a message thread with that person. I am looking for a design that incorporates the colors and ‘feel good’ emotion of our logo. I have pieced together a pretty good interpretation of what I’m looking for in the attached mockup by slicing and dicing designs. I also attached our logo mascot.Screens (see attached mockups)

Note 1: I do not like the picture on the screen used in screen one because it makes it seem like a dating app. I attached an alternative photo that can be used or present different ideas.

Note 2: On the login/signup screen (screen 2) I need an additional first and last name for login, you can try to fit this on one login screen or present a two step signup screen where that is presented in the second screen.

READ MOCKUP GUIDELINES UNDER Must Haves

Target Market(s)

People attending internal social impact events

Industry/Entity Type

Charity

Font styles to use
Sans Serif

Colors
86cfc6

Requirements
Must have
• Follow the screen mockups attached to project
• PLEASE READ
• I have provided a relatively close design of what I’m looking for in the mockups. Some screens need to be followed more closely to my design mockup than other. I have listed a guide below how how closely you should follow my mockup design exactly. Overall I would like to see some ideas of incorporating a few accent colors so it doesn’t appear SO Blue. I also attached some app inspiration designs I found from around the web
• Screen Mockup Guideline Follow %
• Screen 1: 65% - mostly on target, would like to see ways to make it not SO Blue and possibly creative places to add some explainer text describing the app
• Screen 2: 50% - general design idea is here, but more open
• Screen 3: 35% - a lot more room for design influence
• Screen 4: 70% - mostly on target, a little room for design influence/color scheme ideas
• Screen 5-6: 25% - a lot of room for design change/ideas/influence
• Screen 7-8: 80% - already very close to what I need, maybe open to slight sizing and color scheme ideas
• Screen 9: 15% - the most open for influence, only the general functionality of the screen is communicated here
Nice to have
• Please Read Mockup Guideline above. In large part I am looking for something to use some nice accent colors so it is not overwhelmingly blue and bring the whole design into a seamless style.
Should not have

```html
<!DOCTYPE html>
<html lang="en">
<head>
<meta charset="UTF-8">
<title>Add Profile Picture</title>
<link href="https://fonts.googleapis.com/css2?family=Montserrat:wght@300;400;600;700&display=swap" rel="stylesheet">
<style>
  :root {
    --teal: #1fcfc5;
    --teal-glow: rgba(31, 207, 197, 0.35);
    --ink: #1b1b1d;
    --muted: #2b2b2e;
    --surface: #ffffff;
    --line: #2a2a2c;
  }
  * { box-sizing: border-box; margin: 0; padding: 0; }
  html, body {
    width: 1200px;
    height: 2281px;
    overflow: hidden;
    background: var(--surface);
    font-family: "Montserrat", sans-serif;
    color: var(--ink);
  }
  .screen {
    position: relative;
    width: 1200px;
    height: 2281px;
    background: var(--surface);
  }
  .back-button {
    position: absolute;
    left: 120px;
    top: 250px;
    width: 96px;
    height: 64px;
  }
  .page-title {
    position: absolute;
    left: 120px;
    top: 360px;
    line-height: 1.08;
  }
  .page-title .title-light {
    display: block;
    font-weight: 300;
    font-size: 104px;
    letter-spacing: -2px;
  }
  .page-title .title-bold {
    display: block;
    font-weight: 700;
    font-size: 112px;
    letter-spacing: -2px;
  }
  .mascot {
    position: absolute;
    left: 930px;
    top: 380px;
    width: 170px;
    height: 150px;
    border-radius: 50%;
    background: radial-gradient(circle at 40% 40%, #5fdcd3 0%, #1fb8b0 70%, #147f7a 100%);
  }
  .picture-option {
    position: absolute;
    top: 820px;
    width: 340px;
    text-align: center;
  }
  .picture-option.take { left: 160px; }
  .picture-option.browse { left: 700px; }
  .option-tile {
    width: 340px;
    height: 340px;
    border-radius: 70px;
    background: var(--surface);
    box-shadow: 0 0 90px 20px var(--teal-glow);
    display: flex;
    align-items: center;
    justify-content: center;
  }
  .option-tile svg { width: 76px; height: 76px; }
  .option-label {
    margin-top: 70px;
    font-size: 30px;
    font-weight: 600;
    color: var(--muted);
  }
  .next-button {
    position: absolute;
    left: 400px;
    top: 1405px;
    width: 400px;
    height: 110px;
    border-radius: 55px;
    background: var(--teal);
    box-shadow: 0 24px 50px var(--teal-glow);
    color: #fff;
    font-size: 30px;
    font-weight: 700;
    letter-spacing: 2px;
    display: flex;
    align-items: center;
    justify-content: center;
  }
  .skip-button {
    position: absolute;
    left: 640px;
    top: 1890px;
    width: 460px;
    height: 112px;
    border-radius: 56px;
    border: 3px solid var(--line);
    display: flex;
    align-items: center;
    justify-content: space-between;
    padding: 0 26px 0 54px;
    font-size: 30px;
    font-weight: 700;
    letter-spacing: 1.5px;
    color: var(--ink);
  }
  .skip-button svg { width: 64px; height: 64px; }
</style>
</head>
<body>
  <main class="screen">
    <svg class="back-button" viewBox="0 0 96 64" aria-label="Back">
      <path d="M92 32H8M36 4L8 32l28 28" fill="none" stroke="var(--teal)" stroke-width="8" stroke-linecap="round" stroke-linejoin="round"/>
    </svg>

    <h1 class="page-title">
      <span class="title-light">Add Profile</span>
      <span class="title-bold">Picture</span>
    </h1>

    <div class="mascot" role="img" aria-label="App mascot character"></div>

    <div class="picture-option take">
      <div class="option-tile">
        <svg viewBox="0 0 24 24" aria-hidden="true">
          <path d="M4 7h3.5l1.5-2h6l1.5 2H20a1 1 0 0 1 1 1v10a1 1 0 0 1-1 1H4a1 1 0 0 1-1-1V8a1 1 0 0 1 1-1z" fill="none" stroke="var(--teal)" stroke-width="1.8" stroke-linejoin="round"/>
          <circle cx="12" cy="13" r="3.5" fill="none" stroke="var(--teal)" stroke-width="1.8"/>
        </svg>
      </div>
      <p class="option-label">Take Picture</p>
    </div>

    <div class="picture-option browse">
      <div class="option-tile">
        <svg viewBox="0 0 24 24" aria-hidden="true">
          <rect x="3" y="4" width="18" height="16" rx="2" fill="none" stroke="var(--teal)" stroke-width="1.8"/>
          <circle cx="8.5" cy="9" r="1.6" fill="var(--teal)"/>
          <path d="M4 18l5-5 3 3 3-4 5 6z" fill="var(--teal)"/>
        </svg>
      </div>
      <p class="option-label">Browse Picture</p>
    </div>

    <div class="next-button">NEXT</div>

    <div class="skip-button">
      <span>SKIP FOR NOW</span>
      <svg viewBox="0 0 32 32" aria-hidden="true">
        <circle cx="16" cy="16" r="14" fill="none" stroke="var(--ink)" stroke-width="2.5"/>
        <path d="M9 16h13M17 11l5 5-5 5" fill="none" stroke="var(--ink)" stroke-width="2.8" stroke-linecap="round" stroke-linejoin="round"/>
      </svg>
    </div>
  </main>
</body>
</html>
```